Orvane Mechanical - Letterhead

We are a plumbing and hvac company based in Calgary. This letterhead will be on our quotes, invoices, preventative maintenance proposals etc.

```html
<!DOCTYPE html>
<html lang="en">
<head>
<meta charset="utf-8">
<title>Orvane Mechanical – Letterhead</title>
<link rel="stylesheet" href="https://fonts.googleapis.com/css2?family=Lato:wght@400;900&family=Encode+Sans+Semi+Condensed:wght@300&display=swap">
<style>
  :root {
    --backdrop: #d6d6d6;
    --paper: #ffffff;
    --brand-blue: #1f6fbf;
    --brand-orange: #f15a24;
    --body-text: #555555;
    --signature-tint: #fbe3d8;
  }
  * { box-sizing: border-box; margin: 0; padding: 0; }
  html, body {
    width: 1056px; height: 1200px; overflow: hidden;
    background: var(--backdrop);
  }
  .letterhead {
    position: absolute; left: 103px; top: 0;
    width: 849px; height: 1200px;
    background: var(--paper);
    overflow: hidden;
  }
  .brand {
    position: absolute; left: 52px; top: 132px;
    display: flex; align-items: center; gap: 8px;
    font-family: "Lato", sans-serif; font-weight: 900;
    font-size: 21px; line-height: 26px; color: var(--brand-blue);
    text-transform: uppercase; letter-spacing: 0.3px;
  }
  .brand-mark {
    width: 18px; height: 18px; border-radius: 50%;
    background: var(--brand-orange);
  }
  .contact {
    position: absolute; right: 52px; top: 82px;
    font-family: "Lato", sans-serif; font-size: 13.5px; font-style: normal;
    color: var(--brand-blue); text-align: right; line-height: 18px;
  }
  .contact-address { margin-right: 5px; margin-bottom: 9px; }
  .contact-line {
    display: flex; justify-content: flex-end; align-items: center;
    gap: 12px; height: 20.5px;
  }
  .contact-line svg { width: 14px; height: 14px; }
  .accent { color: var(--brand-orange); }
  .header-rule {
    position: absolute; left: 52px; top: 204px;
    width: 745px; height: 1px; background: var(--brand-blue);
  }
  .letter-body {
    position: absolute; left: 82px; top: 367px; width: 689px;
    font-family: "Encode Sans Semi Condensed", sans-serif; font-weight: 300;
    font-size: 18.5px; line-height: 29.5px; color: var(--body-text);
  }
  .letter-body p { text-align: justify; margin-bottom: 29px; }
  .letter-body .salutation { margin-bottom: 26px; }
  .sign-off {
    position: absolute; left: 82px; top: 968px;
    font-family: "Encode Sans Semi Condensed", sans-serif; font-weight: 300;
    font-size: 18.5px; line-height: 29.5px; color: var(--body-text);
  }
  .signature {
    position: absolute; left: 78px; top: 1012px;
    width: 68px; height: 42px; background: var(--signature-tint);
    border-radius: 4px;
  }
  .footer-band {
    position: absolute; left: 0; bottom: 0;
    width: 100%; height: 13px; background: var(--brand-blue);
  }
</style>
</head>
<body>
<main class="letterhead">
  <header>
    <div class="brand"><span class="brand-mark"></span>Orvane Mechanical</div>
    <address class="contact">
      <div class="contact-address">1234 First Line Address<br>5678 Second Line Address</div>
      <div class="contact-line">1234567890
        <svg viewBox="0 0 16 16" aria-hidden="true"><path d="M4 1.5l2.2 2.6-1.3 1.6c.9 2 2.4 3.5 4.4 4.4l1.6-1.3 2.6 2.2-1.4 2.4C7 13.3 2.7 9 1.6 3z" fill="var(--brand-orange)"/></svg>
      </div>
      <div class="contact-line">info@yourmail.com
        <svg viewBox="0 0 16 16" aria-hidden="true"><rect x="1" y="3.5" width="14" height="9.5" fill="var(--brand-orange)"/><path d="M1 3.5l7 5.5 7-5.5M1 13l5-4.5M15 13l-5-4.5" stroke="#fff" stroke-width="1.1" fill="none"/></svg>
      </div>
      <div class="contact-line"><span>www.<span class="accent">yourwebsite</span>.com</span>
        <svg viewBox="0 0 16 16" aria-hidden="true"><g fill="none" stroke="var(--brand-orange)" stroke-width="1.1"><circle cx="8" cy="8" r="6.5"/><ellipse cx="8" cy="8" rx="3" ry="6.5"/><path d="M1.5 8h13M2.5 4.8h11M2.5 11.2h11"/></g></svg>
      </div>
    </address>
    <div class="header-rule"></div>
  </header>

  <section class="letter-body">
    <p class="salutation">Dear Sir/Mam,</p>
    <p>Contrary to popular belief, Lorem Ipsum is not simply random text. It has roots in a piece of classical Latin literature from 45 BC, making it over 2000 years old. Daniel Hartwell, a Latin professor at Westbrook College in Virginia, looked up one of the more obscure Latin words, consectetur.</p>
    <p>Lorem Ipsum comes from sections 1.10.32 and 1.10.33 of "de Finibus Bonorum et Malorum" (The Extremes of Good and Evil) by Varenus, written in 45 BC. This book is a treatise on the theory of ethics, very popular during the Renaissance. The first line of Lorem Ipsum.</p>
    <p>The standard chunk of Lorem Ipsum used since the 1500s is reproduced below for those interested. Sections 1.10.32 and 1.10.33 from "de Finibus Bonorum et Malorum" by Varenus are also reproduced in their exact original.</p>
    <p>The standard chunk of Lorem Ipsum used since the 1500s is reproduced below for those interested.</p>
  </section>

  <div class="sign-off">Best Regards</div>
  <div class="signature" role="img" aria-label="Handwritten signature of the sender"></div>

  <div class="footer-band"></div>
</main>
</body>
</html>
```